Artwork for New Single, ”Keep Still”

Unique design describing Silence.
Use the pictures provided for ideas.
Looking for something out the box, different.
Make this stand out. Modern times or futuristic.
Imagination welcomed.
BRINDLE ENTERTAINMENT INC.
Artist name is Brindle
Song Title: Keep Still

Target Market(s)

Millennials, Trap music listeners, Hardcore rap fans.

Colors

Designer to choose colors to be used in the design.

Requirements
Nice to have
• Bold, serious designs. Make a statement. Masculine, professional in nature.

```html
<!DOCTYPE html>
<html lang="en">
<head>
<meta charset="utf-8">
<title>Keep Still — Brindle — cover options</title>
<link rel="stylesheet" href="https://fonts.googleapis.com/css2?family=Advent+Pro:wght@300&family=Amatic+SC:wght@700&family=Caveat+Brush&family=Josefin+Sans:wght@100&family=Kalam:wght@700&family=Oswald:wght@500&family=Rubik+Dirt&family=Rubik+Wet+Paint&family=Special+Elite&family=Staatliches&family=Teko:wght@600&display=swap">
<style>
  :root {
    --night: #0d1626;
    --ink-blue: #14304f;
    --deep-blue: #1b4470;
    --print-grey: #8a96a6;
    --stamp-red: #e0100f;
    --stamp-dark: #a50b0b;
    --name-white: #f4f6f8;
    --ice-blue: #7fc8f0;
    --seam: #5a6470;
  }
  * { margin: 0; padding: 0; box-sizing: border-box; }
  html, body { width: 1200px; height: 3000px; overflow: hidden; background: var(--night); }
  .cover-sheet {
    display: grid;
    grid-template-columns: repeat(2, 600px);
    grid-template-rows: repeat(5, 600px);
    width: 1200px; height: 3000px;
  }
  .cover {
    position: relative;
    overflow: hidden;
    border: 1px solid var(--seam);
  }
  .cover-art {
    position: absolute; inset: 0;
    background:
      radial-gradient(ellipse 38% 48% at 46% 50%, rgba(138,150,166,0.55), rgba(138,150,166,0) 70%),
      radial-gradient(ellipse 70% 60% at 60% 90%, var(--deep-blue), rgba(27,68,112,0) 70%),
      linear-gradient(160deg, var(--night) 0%, var(--ink-blue) 55%, var(--night) 100%);
  }
  .stamp {
    position: absolute;
    left: 30px; top: 208px;
    width: 545px; height: 160px;
    border-top: 7px solid var(--stamp-red);
    border-bottom: 7px solid var(--stamp-red);
    border-right: 9px solid var(--stamp-dark);
    transform: rotate(4deg);
    transform-origin: left top;
  }
  .stamp-title {
    position: absolute;
    left: 8px; right: 14px; top: 14px;
    font-family: "Rubik Dirt", system-ui, sans-serif;
    font-size: 92px;
    line-height: 1;
    color: var(--stamp-red);
    white-space: nowrap;
    letter-spacing: -3px;
    text-align: center;
  }
  .artist {
    position: absolute;
    left: 0; right: 0; top: 490px;
    text-align: center;
    color: var(--name-white);
    line-height: 1;
    white-space: nowrap;
  }
  .artist--condensed { font-family: "Staatliches", sans-serif; font-size: 66px; letter-spacing: 4px; }
  .artist--drip { font-family: "Rubik Wet Paint", sans-serif; font-size: 72px; top: 480px; }
  .artist--script { font-family: "Caveat Brush", cursive; font-size: 86px; top: 478px; }
  .artist--hairline { font-family: "Josefin Sans", sans-serif; font-weight: 100; font-size: 78px; top: 482px; }
  .artist--spaced { font-family: "Oswald", sans-serif; font-size: 52px; letter-spacing: 22px; padding-left: 22px; top: 500px; }
  .artist--rounded { font-family: "Advent Pro", sans-serif; font-weight: 300; font-size: 58px; letter-spacing: 20px; padding-left: 20px; top: 496px; }
  .artist--sketch { font-family: "Amatic SC", cursive; font-size: 92px; letter-spacing: 8px; top: 474px; }
  .artist--worn { font-family: "Special Elite", monospace; font-size: 58px; letter-spacing: 8px; top: 506px; }
  .artist--ice { font-family: "Teko", sans-serif; font-weight: 600; font-style: italic; font-size: 92px; color: var(--ice-blue); top: 486px; }
  .artist--marker { font-family: "Kalam", cursive; font-size: 64px; top: 510px; }
</style>
</head>
<body>
<main class="cover-sheet">
  <section class="cover">
    <div class="cover-art" role="img" aria-label="Pale handprint over a dark blue background with zippers and swirling lines"></div>
    <div class="stamp"><span class="stamp-title">KEEP STILL</span></div>
    <p class="artist artist--condensed">BRINDLE</p>
  </section>
  <section class="cover">
    <div class="cover-art" role="img" aria-label="Pale handprint over a dark blue background with zippers and swirling lines"></div>
    <div class="stamp"><span class="stamp-title">KEEP STILL</span></div>
    <p class="artist artist--drip">BRINDLE</p>
  </section>
  <section class="cover">
    <div class="cover-art" role="img" aria-label="Pale handprint over a dark blue background with zippers and swirling lines"></div>
    <div class="stamp"><span class="stamp-title">KEEP STILL</span></div>
    <p class="artist artist--script">Brindle</p>
  </section>
  <section class="cover">
    <div class="cover-art" role="img" aria-label="Pale handprint over a dark blue background with zippers and swirling lines"></div>
    <div class="stamp"><span class="stamp-title">KEEP STILL</span></div>
    <p class="artist artist--hairline">BRINDLE</p>
  </section>
  <section class="cover">
    <div class="cover-art" role="img" aria-label="Pale handprint over a dark blue background with zippers and swirling lines"></div>
    <div class="stamp"><span class="stamp-title">KEEP STILL</span></div>
    <p class="artist artist--spaced">BRINDLE</p>
  </section>
  <section class="cover">
    <div class="cover-art" role="img" aria-label="Pale handprint over a dark blue background with zippers and swirling lines"></div>
    <div class="stamp"><span class="stamp-title">KEEP STILL</span></div>
    <p class="artist artist--rounded">BRINDLE</p>
  </section>
  <section class="cover">
    <div class="cover-art" role="img" aria-label="Pale handprint over a dark blue background with zippers and swirling lines"></div>
    <div class="stamp"><span class="stamp-title">KEEP STILL</span></div>
    <p class="artist artist--sketch">BRINDLE</p>
  </section>
  <section class="cover">
    <div class="cover-art" role="img" aria-label="Pale handprint over a dark blue background with zippers and swirling lines"></div>
    <div class="stamp"><span class="stamp-title">KEEP STILL</span></div>
    <p class="artist artist--worn">BRINDLE</p>
  </section>
  <section class="cover">
    <div class="cover-art" role="img" aria-label="Pale handprint over a dark blue background with zippers and swirling lines"></div>
    <div class="stamp"><span class="stamp-title">KEEP STILL</span></div>
    <p class="artist artist--ice">BRINDLE</p>
  </section>
  <section class="cover">
    <div class="cover-art" role="img" aria-label="Pale handprint over a dark blue background with zippers and swirling lines"></div>
    <div class="stamp"><span class="stamp-title">KEEP STILL</span></div>
    <p class="artist artist--marker">Brindle</p>
  </section>
</main>
</body>
</html>
```